Printing Company needs Website

PLEASE REVIEW ALL IMAGES, I HAVE INCLUDED A WEBSITE MOCKUP IDEA AND LOGO FILES IN THESE IMAGES.

Vel-Marks Provides printing services to multiple businesses. We Focus on 4 main markets. Signage (Signs, Banners, Wraps, Custom graphics), Printing (flyers, brochures, business cards, Postcards), Apparel (printed shirts, hoodies, sweatshirts), Promotional Products (mugs, golf balls, brava cans, pens), We try to sell ourselves on total brand imaging, our slogan is "Mark Everything." because we want to be able to provide any type of printing to our customers. Consumer targeting should be targeted towards small business, and wholesale targeting should be geared toward, merchandising, branding, marketing, design, signage, apparel, embroidery, and printing groups. WE DO OFFER DESIGN SERVICES, I have attached one orlwick guild logo design as an example.

I need a website designed both for wholesale and consumer based people. Wholesale customers would have their own login and consumers would also have their own.
I need there to be an online designer software (possibly java) built in so that the customer can order their product or upload their artwork online to see the proof for approval. There will need to be an commence setup, and I do have a quillpay account if that helps. Shipping must be auto calculated at the time of ordering. I would Like to make it to where when customer orders a product if it is outside of the dimensions requested on the site that the customer is warned of clipping or skewing.

I will be working closely aside the designer I pick to aid in the uploading and configuration of pricing structure, weight, and imagery if selected. This will be a lengthy project, and I will be willing to pay for the additional help so long as you are completely aware of the needs, Happy designing!!
Updates

I love all of the designs so far everyone! I will be reviewing PLEASE NOTE, IF I APPROVE YOUR WEB DESIGN, I WILL WANT YOU TO COMPLETE THE ENTIRE DESIGN INCLUDING A DESIGN PROOFING SETUP FOR MY CUSTOMERS INTEGRATED IN AS I HAVE STATED IN THE ORIGINAL STATEMENT. PLEASE ASK QUESTIONS IF YOU DON'T UNDERSTAND!

Target Market(s)

Small Business, School Athletics, Merchandising groups, Branding Groups, Larger Printers, Sign makers, Embroidery shops, Screen Printing Shops

Industry/Entity Type

It Company

Font styles to use
Sans Serif

Colors
000000
1b1b1b
757575
ec1f27

Requirements
Must have
• Built in design setup to each product with sizing, Ability to add pre-designed templates, .pdf print ready files after upload, Wholesale account, or Business accounts all with different pricing structures, Must be willing to aid in setup of all products and services (willing pay additional for setup costs.)
Nice to have
• SEO Optimization, targeting specific groups listed, automatic ordering to outsource vendors straight from site listing drop ship location if need be.

```html
<!DOCTYPE html>
<html lang="en">
<head>
<meta charset="utf-8">
<title>Vel-Marks — Mark Everything.</title>
<link rel="stylesheet" href="https://fonts.googleapis.com/css2?family=Open+Sans:wght@400;600&family=Roboto:wght@100;300&display=swap">
<style>
:root{
  --ink:#000000;
  --base:#1b1b1b;
  --base-deep:#151515;
  --muted:#757575;
  --text-soft:#a9a9a9;
  --white:#ffffff;
  --signage:#e50914;
  --printing:#c5c100;
  --apparel:#46b4b9;
  --promo:#7c0f74;
  --sky-top:#2f5fa8;
  --sky-low:#8fb0d6;
  --wall:#b9b5ac;
  --ground:#6f6a60;
}
*{margin:0;padding:0;box-sizing:border-box}
html,body{width:1200px;height:1036px;overflow:hidden;background:var(--base)}
body{position:relative;font-family:"Open Sans",sans-serif;color:var(--white)}
.hero-photo{position:absolute;left:0;top:0;width:1200px;height:641px;
  background:linear-gradient(180deg,var(--sky-top) 0%,var(--sky-low) 30%,var(--wall) 42%,#8d8a84 58%,#3a3a3c 70%,var(--ground) 86%,#4f4b44 100%)}
.hero-shade{position:absolute;left:0;top:0;width:1200px;height:641px;background:linear-gradient(180deg,rgba(0,0,0,.25),rgba(0,0,0,0) 25%,rgba(0,0,0,.15))}
.main-nav a{position:absolute;top:69px;transform:translateX(-50%);font-size:11px;font-weight:600;color:var(--white);text-decoration:none;letter-spacing:.1px;white-space:nowrap}
.brand{position:absolute;left:600px;top:40px;transform:translateX(-50%);text-align:center;width:260px}
.brand-name{display:flex;align-items:center;justify-content:center;gap:10px;font-family:"Roboto",sans-serif;font-weight:300;font-size:40px;color:var(--white);line-height:1}
.brand-dot{width:16px;height:16px;border-radius:50%;background:var(--signage)}
.brand-tagline{margin-top:8px;font-size:13px;color:var(--white);text-align:right;padding-right:12px}
.hero-title{position:absolute;left:36px;top:360px;font-family:"Roboto",sans-serif;font-weight:100;font-size:86px;color:var(--white);line-height:1;letter-spacing:-1px}
.slider-dots{position:absolute;left:1154px;top:259px}
.slider-dots span{display:block;width:8px;height:8px;border-radius:50%;background:rgba(255,255,255,.85);margin-bottom:16px}
.slider-dots span.is-active{background:transparent;border:1px solid rgba(255,255,255,.7)}
.service-card{position:absolute;width:268px;padding:30px 26px 0;box-shadow:0 10px 14px rgba(0,0,0,.35)}
.service-card h2{font-family:"Roboto",sans-serif;font-weight:300;font-size:21px;line-height:1}
.service-card hr{border:0;height:1px;background:rgba(255,255,255,.85);width:51px;margin:16px 0 10px}
.service-card p{font-size:12px;line-height:24px}
.card-signage{left:42px;top:532px;height:208px;background:var(--signage);padding-top:24px}
.card-signage .card-icon{display:block;margin-bottom:10px}
.card-printing{left:325px;top:601px;height:139px;background:var(--printing)}
.card-apparel{left:608px;top:601px;height:139px;background:var(--apparel)}
.card-apparel p,.card-promo p{line-height:22px}
.card-promo{left:890px;top:601px;height:139px;background:var(--promo)}
.footer-col{position:absolute;top:793px}
.footer-col h3{font-family:"Roboto",sans-serif;font-weight:300;font-size:20px;color:var(--white);margin-bottom:14px}
.footer-col p{font-size:12px;color:var(--text-soft);line-height:21px}
.footer-links{list-style:none;font-size:11.5px;line-height:24px;color:var(--text-soft)}
.follow{left:58px}
.social{display:flex;gap:7px;margin-top:18px}
.social span{width:34px;height:34px;border-radius:50%}
.welcome{left:396px}
.welcome .link-grid{display:flex;gap:70px}
.information{left:681px}
.newsletter{left:896px;width:264px}
.email-field{margin-top:18px;height:38px;border:1px solid #3a3a3a;display:flex;align-items:center;justify-content:space-between;padding:0 10px 0 16px;font-size:12px;color:var(--text-soft)}
.site-bottom{position:absolute;left:0;top:989px;width:1200px;height:47px;background:var(--base-deep);text-align:center;line-height:47px;font-size:11.5px;color:var(--text-soft)}
</style>
</head>
<body>
<div class="hero-photo" role="img" aria-label="Photo of a restaurant building with large printed window graphics and parked cars"></div>
<div class="hero-shade"></div>

<nav class="main-nav">
  <a style="left:98px">HOME</a>
  <a style="left:195px">SIGNAGE</a>
  <a style="left:300px">PRINTING</a>
  <a style="left:401px">DESIGN</a>
  <a style="left:798px">PROMOTIONAL</a>
  <a style="left:909px">APPAREL</a>
  <a style="left:1009px">ABOUT US</a>
  <a style="left:1119px">CONTACT US</a>
</nav>

<div class="brand">
  <div class="brand-name"><span class="brand-dot"></span>Vel-Marks</div>
  <div class="brand-tagline">Mark Everything.</div>
</div>

<h1 class="hero-title">Mark Everything</h1>

<div class="slider-dots"><span class="is-active"></span><span></span><span></span><span></span><span></span></div>

<section class="service-card card-signage">
  <svg class="card-icon" width="58" height="60" viewBox="0 0 58 60" fill="none" stroke="#fff" stroke-width="3" stroke-linejoin="round">
    <path d="M27 2v56"/>
    <path d="M4 8h44l8 7-8 7H4z"/>
    <path d="M52 27H10l-8 7 8 7h42z"/>
  </svg>
  <h2>Signage</h2><hr>
  <p>Signs, Banners, Wraps, Custom graphics</p>
</section>
<section class="service-card card-printing">
  <h2>Printing</h2><hr>
  <p>Flyers, Brochures, Business cards, Postcards</p>
</section>
<section class="service-card card-apparel">
  <h2>Apparel</h2><hr>
  <p>Printed shirts, Hoodies,<br>Sweatshirts</p>
</section>
<section class="service-card card-promo">
  <h2>Promotional Products</h2><hr>
  <p>Mugs, Golf balls, Brava cans,<br>Pens</p>
</section>

<footer>
  <div class="footer-col follow">
    <h3>Follow Us</h3>
    <p>Connect with our social network</p>
    <div class="social">
      <span style="background:#ea4c89"></span>
      <span style="background:#3cb2e6"></span>
      <span style="background:#1b7ea6"></span>
      <span style="background:#dc2127"></span>
      <span style="background:#2a66b6"></span>
      <span style="background:#f0a11d"></span>
    </div>
  </div>
  <div class="footer-col welcome">
    <h3>Welcome</h3>
    <div class="link-grid">
      <ul class="footer-links"><li>Home</li><li>Signage</li><li>Printing</li><li>Design</li><li>Promotional</li></ul>
      <ul class="footer-links"><li>Apparel</li><li>About Us</li><li>Contact us</li></ul>
    </div>
  </div>
  <div class="footer-col information">
    <h3>Information</h3>
    <ul class="footer-links"><li>Terms &amp; Conditions</li><li>Privacy Policy</li><li>Disclaimer</li><li>Sitemap</li></ul>
  </div>
  <div class="footer-col newsletter">
    <h3>Newsletter signup</h3>
    <p>Get our recent updates through your email id</p>
    <div class="email-field">Enter your email id
      <svg width="20" height="10" viewBox="0 0 20 10" fill="none" stroke="#a9a9a9" stroke-width="1.3"><path d="M0 5h19M14 1l5 4-5 4"/></svg>
    </div>
  </div>
  <div class="site-bottom">Copyright © 2016. Vel-Marks. All rights reserved.</div>
</footer>
</body>
</html>
```